Law Offices business card

Hi there, I'll need business card for the Law Offices of Colin Matheny. The information must convey his strategic approach and quick resolution to complex business litigation needs. Please emphasize Civil Litigation, Corporate Law, Business Governance and Real Estate Law. Colin has over 25 years of experience in these fields.The card should be modern and edgy and the message should be clear. Please consult his current website for ideas.

```html
<!DOCTYPE html>
<html lang="en">
<head>
<meta charset="utf-8">
<title>Law Offices of Colin Matheny – Business Card</title>
<link rel="stylesheet" href="https://fonts.googleapis.com/css2?family=Arimo:wght@400&family=Tinos:wght@400;700&display=swap">
<style>
  :root {
    --backdrop: #e9e7e3;
    --paper: #ffffff;
    --ink: #000000;
    --olive: #b0ad36;
    --light-text: #ffffff;
    --card-shadow: 0 6px 14px rgba(0,0,0,0.35);
  }
  * { margin: 0; padding: 0; box-sizing: border-box; }
  html, body { width: 1189px; height: 1200px; overflow: hidden; }
  body { background: var(--backdrop); position: relative; }

  .card {
    position: absolute;
    left: 140px;
    width: 918px;
    box-shadow: var(--card-shadow);
    overflow: hidden;
  }
  .card-front { top: 45px; height: 524px; background: var(--paper); }
  .card-back { top: 624px; height: 522px; background: var(--olive); }

  .line {
    position: absolute;
    left: 0; right: 0;
    text-align: center;
    line-height: 1;
    white-space: nowrap;
  }
  .serif { font-family: "Tinos", "Times New Roman", serif; }
  .sans { font-family: "Arimo", Helvetica, Arial, sans-serif; }

  .attorney-name { top: 64px; font-size: 58px; font-weight: 700; color: var(--ink); }
  .attorney-title { top: 126px; font-size: 34px; color: var(--ink); }
  .firm-name { top: 188px; font-size: 40px; font-weight: 700; color: var(--ink); }

  .wave { position: absolute; inset: 0; width: 918px; height: 524px; }
  .wave-accent { fill: var(--olive); }
  .wave-base { fill: var(--ink); }

  .contact { font-size: 27px; color: var(--light-text); }
  .contact-phone-main { top: 318px; }
  .contact-phone-alt { top: 357px; }
  .contact-email { top: 397px; }
  .contact-web { top: 437px; }
  .contact-address { top: 475px; }

  .services-heading { top: 103px; font-size: 65px; font-weight: 700; color: var(--ink); }
  .services-rule {
    position: absolute;
    left: 86px;
    width: 744px;
    top: 192px;
    height: 2px;
    background: var(--ink);
  }
  .service { font-size: 34px; color: var(--ink); }
  .service-litigation { top: 226px; }
  .service-corporate { top: 289px; }
  .service-governance { top: 357px; }
</style>
</head>
<body>
  <section class="card card-front" aria-label="Business card front">
    <svg class="wave" viewBox="0 0 918 524" aria-hidden="true">
      <path class="wave-accent" d="M0 252 C90 275 180 292 268 290 C420 286 560 236 692 237 C790 238 860 258 918 282 L918 524 L0 524 Z"/>
      <path class="wave-base" d="M0 302 C90 318 170 324 251 322 C400 318 540 252 667 253 C780 254 860 275 918 302 L918 524 L0 524 Z"/>
    </svg>
    <h1 class="line serif attorney-name">Colin Matheny</h1>
    <p class="line sans attorney-title">Attorney</p>
    <p class="line serif firm-name">Law Offices of Colin Matheny, P.A.</p>
    <p class="line sans contact contact-phone-main">555-013-4829</p>
    <p class="line sans contact contact-phone-alt">555-017-6203</p>
    <p class="line sans contact contact-email">colin@mathenylaw.com</p>
    <p class="line sans contact contact-web">www.mathenylaw.com</p>
    <p class="line sans contact contact-address">118B Harbor Lane, Coral Bay, Florida 33999</p>
  </section>

  <section class="card card-back" aria-label="Business card back">
    <h2 class="line serif services-heading">Services</h2>
    <div class="services-rule"></div>
    <p class="line sans service service-litigation">Civil Litigation</p>
    <p class="line sans service service-corporate">Corporate Law</p>
    <p class="line sans service service-governance">Business Governance and Real Estate Law</p>
  </section>
</body>
</html>
```